Letterhead and matching envelope design for a dental office

We need a new stationary design, letterhead and envelope #10, for a dental office in Denver area. We are called Bright Harbor Dental. We want a simple and minimalistic design but not a boring design. I wish to have one good point that makes it look professional. I have attached our logo. Feel free to use either one. I want the design for letterhead and envelope look like a "matching pair" but not look the same. The envelope doesn't have to be white and it will have an address window on bottom left.

Target Market(s)

everyone who visits dentist (adults)

Industry/Entity Type

Dental

Font styles to use
Other font styles liked:
• close to font on logo or something that matches well

Requirements
Must have
• professional
• simple, minimalistic
• unique point that stands out
Nice to have
• matching but not same design for letterhead and envelope
Should not have
• not look like all the other boring designs
• no flowery, distracting feats

```html
<!DOCTYPE html>
<html lang="en">
<head>
<meta charset="utf-8">
<title>Bright Harbor Dental – Letterhead</title>
<link rel="stylesheet" href="https://fonts.googleapis.com/css2?family=Arimo:wght@400;700&family=Open+Sans:wght@400;600;700&display=swap">
<style>
  :root {
    --backdrop: #8f8a85;
    --paper: #ffffff;
    --brand-green: #3bb44a;
    --brand-green-light: #8fd496;
    --ink: #3a3a3a;
    --ink-soft: #555555;
    --rule: #9ad3a0;
  }
  * { box-sizing: border-box; margin: 0; padding: 0; }
  html, body {
    width: 1200px; height: 795px; overflow: hidden;
    background: var(--backdrop);
  }
  .letterhead {
    position: absolute; left: 333px; top: 20px;
    width: 534px; height: 755px;
    background: var(--paper);
    box-shadow: 0 4px 14px rgba(0,0,0,.25);
    overflow: hidden;
  }
  .header-wave { position: absolute; left: 0; top: 0; width: 534px; height: 160px; }
  .header-web {
    position: absolute; right: 26px; top: 20px;
    font: 400 9px "Open Sans", sans-serif; color: #fff; letter-spacing: .4px;
  }
  .brand-mark {
    position: absolute; left: 34px; top: 176px;
    display: flex; align-items: center; gap: 7px;
  }
  .brand-dot { width: 12px; height: 12px; border-radius: 50%; background: var(--brand-green); }
  .brand-name {
    font: 700 11px "Open Sans", sans-serif; color: var(--brand-green);
    letter-spacing: 1.2px; text-transform: uppercase;
  }
  .letter-body {
    position: absolute; left: 44px; top: 236px; width: 446px;
    font: 400 9.4px/1.3 "Arimo", sans-serif; color: var(--ink-soft);
  }
  .salutation { font: 700 11px "Arimo", sans-serif; color: var(--ink); margin-bottom: 8px; }
  .letter-body p { margin-bottom: 11px; text-align: justify; }
  .signature {
    position: absolute; left: 56px; top: 452px; width: 118px; height: 44px;
    background: linear-gradient(90deg, #e9e9e9, #d9d9d9);
    border-radius: 4px;
  }
  .footer-rule {
    position: absolute; left: 30px; right: 30px; top: 628px;
    height: 1px; background: var(--rule);
  }
  .footer-contact {
    position: absolute; right: 38px; top: 640px; text-align: right;
    font: 400 9px/1.55 "Open Sans", sans-serif; color: var(--ink);
  }
  .footer-name { font-weight: 700; color: var(--brand-green); font-size: 9.5px; }
  .footer-line { display: flex; justify-content: flex-end; align-items: center; gap: 4px; }
  .contact-icon { width: 10px; height: 10px; }
</style>
</head>
<body>
  <main class="letterhead">
    <svg class="header-wave" viewBox="0 0 534 160" aria-hidden="true">
      <path d="M0 0 H534 V40 C430 50 340 80 250 108 C160 135 70 140 0 132 Z" fill="var(--brand-green)"/>
      <path d="M0 140 C75 148 165 143 255 116 C345 88 435 58 534 48" fill="none" stroke="var(--brand-green-light)" stroke-width="2"/>
      <path d="M0 148 C80 156 172 150 262 122 C352 94 440 64 534 56" fill="none" stroke="var(--brand-green-light)" stroke-width="1"/>
    </svg>
    <div class="header-web">www.brightharbordental.com</div>

    <div class="brand-mark">
      <span class="brand-dot"></span>
      <span class="brand-name">Bright Harbor Dental</span>
    </div>

    <section class="letter-body">
      <div class="salutation">Dear Mr. Avery,</div>
      <p>Lorem Ipsum is simply dummy text of the printing and typesetting industry. Lorem Ipsum has been the industry's standard dummy text ever since the 1500s, when an unknown printer took a galley of type and scrambled it to make a type specimen book. It has survived not only five centuries, but also the leap into electronic typesetting, remaining essentially unchanged.</p>
      <p>The standard chunk of Lorem Ipsum used since the 1500s is reproduced below for those interested. Sections 1.10.32 and 1.10.33 from "de Finibus Bonorum et Malorum" by Cicero are also reproduced in their exact original form, accompanied by English versions from the 1914 translation by H. Rackham.</p>
      <p>Lorem Ipsum is simply dummy text of the printing and typesetting industry. Lorem Ipsum has been the industry's standard dummy text ever since the 1500s, when an unknown printer took a galley of type and scrambled it to make a type specimen book. It has survived not only five centuries, but also the leap into electronic typesetting, remaining essentially unchanged. It was popularised in the</p>
    </section>

    <div class="signature" role="img" aria-label="Handwritten signature of the sender"></div>

    <div class="footer-rule"></div>

    <footer class="footer-contact">
      <div class="footer-name">Bright Harbor Dental</div>
      <div>4120 MEADOW RIDGE BLVD, SUITE 210 LAKEWOOD, CO 80228</div>
      <div class="footer-line">
        <svg class="contact-icon" viewBox="0 0 10 10" aria-hidden="true"><circle cx="5" cy="5" r="5" fill="var(--brand-green)"/><path d="M3.2 2.6 L4.2 2.4 L4.6 3.7 L4 4.2 C4.3 4.9 4.8 5.5 5.6 5.9 L6.1 5.3 L7.4 5.7 L7.3 6.7 C5.1 7 2.9 4.9 3.2 2.6 Z" fill="#fff"/></svg>
        <span>720-555-0142</span>
        <svg class="contact-icon" viewBox="0 0 10 10" aria-hidden="true"><circle cx="5" cy="5" r="5" fill="var(--brand-green)"/><rect x="2.5" y="3.2" width="5" height="3.6" fill="none" stroke="#fff" stroke-width=".7"/><path d="M2.5 3.2 L5 5.2 L7.5 3.2" fill="none" stroke="#fff" stroke-width=".7"/></svg>
        <span>hello@brightharbordental.com</span>
      </div>
    </footer>
  </main>
</body>
</html>
```